Creation of a Velmaro website

Velmaro is a company% 26 # 233; t% 26 # 233; consulting that accompanies Swiss companies or% 26 # 233; strang% 26 # 232; res in the d% 26 # 233; development of their business on the market% 26 # 233; Switzerland by providing strategic contacts (personalized contact program% 26 # 233; s) or market information% 26 # 233; (% 26 # 233; market research% 26 # 233;) and by providing administrative support (repr% 26 # 233; tax representation) or logistics (organization of% 26 # 233; v% 26 # 233; nement, assistance for participation% 26 # 224; fairs). Our customers are mainly European companies wishing to develop their business in Switzerland. N% 26 # 233; however, our services are% 26 # 233; also aimed at Swiss companies wishing to develop in other parts of Switzerland. Our site must therefore be% 26 # 234; capable of being translated into several languages. The services offered% 26 # 233; s by Velmaro may also% 26 # 233; also% 26 # 39;% 26 # 233; tender% 26 # 224; promoting tourism in Switzerland for countries or regions% 26 # 233; foreigners or% 26 # 224; the promotion of trade fairs or fairs with% 26 # 232; sd% 26 # 39; companies of the sectors concerned% 26 # 233; s. It is therefore n% 26 # 233; necessary to be able to add sub-headings of services which can% 26 # 234; be displayed% 26 # 233; es or hide% 26 # 233; es as required. We are 2 associates% 26 # 233; s, low% 26 # 233; s in the French-speaking parts (Neuch% 26 # 226; tel) and al% 26 # 233; manique (Zurich) of Switzerland.

Target Market(s)

Swiss or European companies wishing to develop their activities in Switzerland.

Coding

Coded - Design and coding required

Colors

Designer to choose colors to be used in the design.

Requirements
Must have
• A home page A section of% 26 # 233; writing the services offered% 26 # 233; es by Velmaro with the possibility% 26 # 233; d% 26 # 39; add sub-headings which can% 26 # 234; be displayed% 26 # 233; e or hidden% 26 # 233; e A page with the r% 26 # 233; f% 26 # 233; which can be displayed% 26 # 233; e or hidden% 26 # 233; e A page of% 26 # 233; writing l% 26 # 39;% 26 # 233; team A page with form contact, addresses and int card% 26 # 233; gr% 26 # 233; e The site must% 26 # 234; be low% 26 # 233; on a CMS allowing% 26 # 39;% 26 # 234; to be autonomous in modifying the website The possibility% 26 # 233; to be able to translate the site into several languages (FR, EN, DE, IT, NL, ...)

```html
<!DOCTYPE html>
<html lang="en">
<head>
<meta charset="utf-8">
<title>Velmaro — Business Consulting</title>
<link href="https://fonts.googleapis.com/css2?family=Poppins:wght@300;400;500;600&family=Montserrat:wght@200;300&display=swap" rel="stylesheet">
<style>
:root{
  --navy:#1d3a52;
  --navy-deep:#16304a;
  --steel:#3a6f93;
  --ink:#2b2b2b;
  --text:#4a4a4a;
  --muted:#6b6b6b;
  --white:#ffffff;
  --line:#b9c0c6;
}
*{margin:0;padding:0;box-sizing:border-box}
html,body{width:1200px;height:3598px;overflow:hidden}
body{position:relative;font-family:"Poppins",sans-serif;color:var(--text);background:var(--white)}
.abs{position:absolute}

/* hero */
.hero-bg{left:0;top:0;width:1200px;height:800px}
.brand{left:112px;top:42px;display:flex;align-items:center;gap:18px;color:var(--white)}
.brand-square{width:50px;height:50px;border-radius:10px;background:var(--white)}
.brand-name{font-family:"Poppins",sans-serif;font-weight:300;font-size:40px;letter-spacing:4px}
.lang{left:962px;top:14px;width:125px;height:42px;border:2px solid var(--white);border-radius:21px;color:var(--white);font-size:17px;display:flex;align-items:center;justify-content:center;gap:10px}
.lang-flag{width:44px;height:26px;background:#2c3f7a;border-radius:3px}
.nav{left:572px;top:64px;display:flex;gap:18px;font-size:16px;font-weight:500;color:var(--white)}
.nav a{color:inherit;text-decoration:none;padding:4px 10px}
.nav .active{background:rgba(255,255,255,.25);border-radius:14px}
.hero-title{left:0;top:190px;width:1200px;text-align:center;font-family:"Montserrat",sans-serif;font-weight:200;font-size:92px;letter-spacing:10px;color:var(--white)}
.hero-sub{left:190px;top:312px;width:820px;text-align:center;font-size:16px;line-height:25px;color:var(--white)}

/* service cards */
.card{color:var(--white);text-align:center;background:linear-gradient(100deg,#545454,#2a2a2a);border:3px solid #e9e9e9}
.card-l{left:112px;top:521px;width:300px;height:248px}
.card-r{left:789px;top:521px;width:298px;height:248px}
.card-m{left:412px;top:496px;width:377px;height:300px;background:linear-gradient(100deg,#1c3a56,#3a6f93);border-color:#e9e9e9;z-index:2}
.card svg{margin-top:30px}
.card h3{font-weight:500;font-size:23px;margin-top:8px}
.card-m h3{font-size:28px;margin-top:10px}
.card p{font-size:11.5px;line-height:21px;margin:12px 16px 0}
.card-m p{font-size:14px;line-height:25px;margin:14px 22px 0}

/* intro */
.intro-title{left:112px;top:900px;font-size:36px;line-height:44px;color:var(--navy);font-weight:400}
.intro-title b{font-weight:600}
.intro-copy{left:112px;top:1006px;width:525px;font-size:14px;line-height:24px}
.intro-copy p+p{margin-top:10px}
.btn{display:flex;align-items:center;justify-content:center;background:var(--navy);color:var(--white);font-weight:500;border-radius:10px}
.intro-btn{left:112px;top:1187px;width:125px;height:58px;font-size:17px}
.intro-photo{left:679px;top:873px;width:409px;height:409px;border-radius:84px;background:linear-gradient(135deg,#48657f,#1f3b55 60%,#2d4a63)}

/* process */
.process{left:0;top:1379px;width:1200px;height:539px;background:var(--navy)}
.sec-title{width:1200px;left:0;text-align:center;font-weight:600;font-size:35px}
.sec-sub{left:180px;width:840px;text-align:center;font-size:14px;line-height:24px}
.step{width:230px;text-align:center;color:var(--white)}
.step-num{width:118px;height:118px;margin:0 auto;border:3px solid var(--white);border-radius:50%;display:flex;align-items:center;justify-content:center;font-size:52px;font-weight:600;background:var(--navy)}
.step-num.shade{background:linear-gradient(180deg,#8497a8,#2b4660)}
.step h4{font-weight:400;font-size:24px;margin-top:24px}
.step p{font-size:14px;line-height:23px;margin-top:6px}

/* skills */
.skills-photo{left:0;top:1918px;width:600px;height:503px;background:linear-gradient(120deg,#e8e4dc,#b8b2a6 45%,#5a5f66 75%,#c9a86a)}
.skills-title{left:633px;top:1984px;font-size:29px;line-height:35px;color:var(--navy)}
.skills-copy{left:633px;top:2052px;width:455px;font-size:13.5px;line-height:21px}
.stat{width:210px}
.stat strong{display:block;font-size:44px;font-weight:600;color:var(--navy);line-height:50px}
.stat span{display:block;font-size:17px;font-weight:500;color:var(--navy);margin-top:2px}
.stat p{font-size:13px;line-height:19px;margin-top:6px;text-align:justify}
.skills-btn{left:633px;top:2324px;width:113px;height:51px;font-size:15px}

/* testimonials */
.say-band{left:0;top:2421px;width:1200px;height:261px;background:linear-gradient(100deg,#2c4a63,#1d3a52 55%,#244560)}
.say-title{right:112px;top:2500px;font-size:36px;font-weight:600;color:var(--white)}
.say-sub{left:300px;top:2560px;width:788px;text-align:right;font-size:14px;line-height:24px;color:var(--white)}
.avatar{left:112px;top:2599px;width:162px;height:162px;border-radius:50%;border:4px solid var(--white);background:linear-gradient(160deg,#cfc4b8,#8b7a6c)}
.person{left:93px;top:2770px;width:200px;text-align:center}
.person b{display:block;font-weight:400;font-size:17px;color:var(--navy)}
.person span{font-size:15px;color:var(--ink)}
.quote{left:415px;top:2723px;width:673px;font-size:16px;line-height:28px;color:var(--ink)}

/* contact */
.contact-bg{left:0;top:2892px;width:1200px;height:617px;background:linear-gradient(180deg,#f2f2f2,#ffffff 30%)}
.field{left:112px;width:532px;border:1.5px solid #9aa1a7;background:var(--white);font-size:13px;padding:14px 12px;color:var(--ink)}
.send-btn{left:112px;top:3372px;width:110px;height:52px;font-size:15px}
.info{left:718px;display:flex;align-items:center;gap:12px;font-size:18px;color:var(--ink);line-height:26px}
.info-ico{width:62px;height:62px;border:2px solid var(--navy);border-radius:50%;flex:none;display:flex;align-items:center;justify-content:center}

.footer{left:0;top:3509px;width:1200px;height:89px;background:var(--white);text-align:center;line-height:89px;font-size:17px;color:var(--ink);border-top:1px solid #eee}
</style>
</head>
<body>

<!-- hero -->
<svg class="abs hero-bg" viewBox="0 0 1200 800" role="img" aria-label="Photo of a hand working with a calculator and financial papers on a desk">
  <defs>
    <linearGradient id="heroGrad" x1="0" y1="0" x2="1" y2="1">
      <stop offset="0" stop-color="#3d3d3d"/>
      <stop offset=".5" stop-color="#6e6e6e"/>
      <stop offset="1" stop-color="#4a4a4a"/>
    </linearGradient>
  </defs>
  <path d="M0 0H1200V600Q600 820 0 600Z" fill="url(#heroGrad)"/>
</svg>

<div class="abs brand"><span class="brand-square"></span><span class="brand-name">VELMARO</span></div>
<div class="abs lang"><span class="lang-flag"></span>Eng ▾</div>
<nav class="abs nav">
  <a class="active">Home</a><a>About Us</a><a>Our Pricing</a><a>Portfolio</a><a>Our Blog</a><a>Contact Us</a>
</nav>
<h1 class="abs hero-title">VELMARO</h1>
<p class="abs hero-sub">Nemo enim ipsam voluptatem quia voluptas sit aspernatur aut odit aut fugit, sed quia consequuntur magni dolores eos qui ratione voluptatem.</p>

<div class="abs card card-l">
  <svg width="56" height="56" viewBox="0 0 56 56" fill="none" stroke="#fff" stroke-width="2"><path d="M10 4h24l10 10v36H10z"/><path d="M34 4v10h10"/><path d="M16 22h14M16 30h8M16 38h8"/><circle cx="34" cy="34" r="8"/><path d="M40 40l10 10M30 34h8"/></svg>
  <h3>Logistics</h3>
  <p>Velmaro is a company consulting that accompanies Swiss companies or strangers in the development of their business.</p>
</div>
<div class="abs card card-m">
  <svg width="64" height="64" viewBox="0 0 56 56" fill="none" stroke="#fff" stroke-width="2"><path d="M10 4h24l10 10v36H10z"/><path d="M34 4v10h10"/><path d="M16 22h14M16 30h8M16 38h8"/><circle cx="34" cy="34" r="8"/><path d="M40 40l10 10M30 34h8"/></svg>
  <h3>Market Research</h3>
  <p>Velmaro is a company consulting that accompanies Swiss companies or strangers in the development of their business.</p>
</div>
<div class="abs card card-r">
  <svg width="56" height="56" viewBox="0 0 56 56" fill="none" stroke="#fff" stroke-width="2"><path d="M10 4h24l10 10v36H10z"/><path d="M34 4v10h10"/><path d="M16 22h14M16 30h8M16 38h8"/><circle cx="34" cy="34" r="8"/><path d="M40 40l10 10M30 34h8"/></svg>
  <h3>Tax Representation</h3>
  <p>Velmaro is a company consulting that accompanies Swiss companies or strangers in the development of their business.</p>
</div>

<!-- intro -->
<h2 class="abs intro-title"><b>Lets take your Business</b><br>to Next Level</h2>
<div class="abs intro-copy">
  <p>Lorem ipsum dolor sit amet, consectetur adipiscing elit. Nunc mauris arcu, lobortis id interdum vitae, interdum eget elit. Curabitur quis urna nulla. Sus pendisse potenti. Duis suscipit ultrices maximus.</p>
  <p>Sed ut perspiciatis unde omnis iste natus error sit voluptatem accusantium doloremque laudantium, totam rem aperiam, eaque ipsa quae ab illo inven tore veritatis et quasi vitae dicta sunt explicabo.</p>
</div>
<div class="abs btn intro-btn">Read More</div>
<div class="abs intro-photo" role="img" aria-label="Photo of colleagues discussing documents at a meeting table, tinted blue"></div>

<!-- process -->
<section class="abs process">
  <h2 class="abs sec-title" style="top:74px;color:var(--white)">Our Work Process</h2>
  <p class="abs sec-sub" style="top:134px;color:var(--white)">Sed ut perspiciatis unde omnis iste natus error sit voluptatem accusantium doloremque laudantium, totam rem aperiam, eaque ipsa quae ab illo inven tore dicta sunt explicabo.</p>
  <svg class="abs" style="left:0;top:0" width="1200" height="539"><path d="M277 304H416M535 304H663M782 304H920" stroke="#c9d3dc" stroke-width="1.5" stroke-dasharray="4 3"/></svg>
  <div class="abs step" style="left:102px;top:245px"><div class="step-num shade">01</div><h4>Concept</h4><p>Quisque tellus risus, adipisci<br>viverra urna.</p></div>
  <div class="abs step" style="left:360px;top:245px"><div class="step-num">02</div><h4>Plan</h4><p>Quisque tellus risus, adipisci<br>viverra urna.</p></div>
  <div class="abs step" style="left:607px;top:245px"><div class="step-num shade">03</div><h4>Development</h4><p>Quisque tellus risus, adipisci<br>viverra urna.</p></div>
  <div class="abs step" style="left:864px;top:245px"><div class="step-num">04</div><h4>Quality Check</h4><p>Quisque tellus risus, adipisci<br>viverra urna.</p></div>
</section>

<!-- skills -->
<div class="abs skills-photo" role="img" aria-label="Photo of a presenter at a whiteboard speaking to a team in an office"></div>
<h2 class="abs skills-title">We’re Constantly Improving Our<br>Skills to Fulfill Projects</h2>
<p class="abs skills-copy">Sed ut perspiciatis unde omnis iste natus error sit voluptatem ac cusantium doloremque laudantium, totam rem aperiam, eaque ipsa quae ab illo inven.</p>
<div class="abs stat" style="left:633px;top:2142px"><strong>650 +</strong><span>Team Members</span><p>Lorem ipsum dolor sit amet, consectetur adipiscing elit, sed do eiusmod.</p></div>
<div class="abs stat" style="left:879px;top:2142px"><strong>3800 +</strong><span>Happy Clients</span><p>Lorem ipsum dolor sit amet, consectetur adipiscing elit, sed do eiusmod.</p></div>
<div class="abs btn skills-btn">Read More</div>

<!-- testimonials -->
<div class="abs say-band" role="img" aria-label="Dark blue tinted photo of hands holding a phone"></div>
<h2 class="abs say-title">What People Say</h2>
<p class="abs say-sub">Sed ut perspiciatis unde omnis iste natus error sit voluptatem accusantium doloremque laudantium, totam rem aperiam, eaque ipsa quae ab illo inven tore dicta sunt explicabo.</p>
<div class="abs avatar" role="img" aria-label="Portrait photo of the client"></div>
<div class="abs person"><b>Daniel Ferris</b><span>Northgate, New York</span></div>
<svg class="abs" style="left:54px;top:2762px" width="270" height="32" fill="none" stroke="#5a6b7a" stroke-width="2.5"><path d="M22 4L10 16l12 12"/><path d="M248 4l12 12-12 12"/></svg>
<p class="abs quote">Nemo enim ipsam voluptatem quia voluptas sit aspernatur aut odit aut fugit, sed quia consequuntur magni dolores eos qui ratione voluptatem sequi nesci unt quasi archi tecto beatae vitae dicta sunt explicabo.</p>

<!-- contact -->
<div class="abs contact-bg"></div>
<h2 class="abs sec-title" style="top:2962px;color:var(--navy)">Contact Us</h2>
<p class="abs sec-sub" style="top:3022px;color:var(--text)">Sed ut perspiciatis unde omnis iste natus error sit voluptatem accusantium doloremque laudantium, totam rem aperiam, eaque ipsa quae ab illo inven tore dicta sunt explicabo.</p>
<div class="abs field" style="top:3127px;height:56px">Name</div>
<div class="abs field" style="top:3195px;height:56px">Email</div>
<div class="abs field" style="top:3263px;height:91px">Message</div>
<div class="abs btn send-btn">Send Now</div>

<div class="abs info" style="top:3132px">
  <span class="info-ico"><svg width="28" height="28" viewBox="0 0 24 24" fill="none" stroke="#1d3a52" stroke-width="1.5"><path d="M12 22s7-7 7-12a7 7 0 0 0-14 0c0 5 7 12 7 12z"/><circle cx="12" cy="10" r="2.5"/></svg></span>
  <span>Address: 42 Harrow Lane,<br>EC2A 7QT</span>
</div>
<div class="abs info" style="top:3207px">
  <span class="info-ico"><svg width="28" height="28" viewBox="0 0 24 24" fill="none" stroke="#1d3a52" stroke-width="1.5"><path d="M5 3h4l2 5-3 2a12 12 0 0 0 6 6l2-3 5 2v4a2 2 0 0 1-2 2A18 18 0 0 1 3 5a2 2 0 0 1 2-2z"/></svg></span>
  <span>+ 123 555 0148</span>
</div>
<div class="abs info" style="top:3280px">
  <span class="info-ico"><svg width="28" height="28" viewBox="0 0 24 24" fill="none" stroke="#1d3a52" stroke-width="1.5"><rect x="3" y="5" width="18" height="14"/><path d="M3 5l9 8 9-8"/></svg></span>
  <span>info@velmaro.com</span>
</div>

<footer class="abs footer">Copyrights @ Velmaro. All Rights Reserved.</footer>

</body>
</html>
```